New eyelid plastic surgery office needs a business card design-Eyelid Care Partners of the Brenton

I recently used PixelForge for my logo design and was very pleased with creativity and results. It was a difficult decision for me. Now I would like to create a business card based on this logo, which I will attach.

The text should be easily legible as some of my patients have difficulty seeing, but I would like a subtle, sophisticated artistry also evident to make the card memorable. Would like the card based on a similar color scheme as the logo but the inverse or other complementary colors may prove interesting
Updates

A good question was asked...my concern about my visually impaired patients was really my desire to avoid italicized or calligraphic type fonts that may be hard to read. Standard font size for a business card would be fine. Thanks!

Thank you so much for the great work so far. I wanted to give you my particular contact information to see if that would change the look of the cards. Martin Delacourt, MD Address: 2718 Harborview Lane, Suite 206 Lakemont, VT 28517 Phone: 555-555-0193 Fax: 555-555-0194 Website: www.brentonlidstudio.example Please delete the email slot from the card. Thanks so much!

Industry/Entity Type

Plastic

```html
<!DOCTYPE html>
<html lang="en">
<head>
<meta charset="utf-8">
<title>Eyelid Care Partners of the Brenton – Business Card</title>
<link rel="stylesheet" href="https://fonts.googleapis.com/css2?family=Arimo:wght@700&display=swap">
<style>
  :root {
    --page: #f3e6d2;
    --grey-light: #9a9a9a;
    --grey-mid: #7e7e7e;
    --grey-dark: #3c3c3c;
    --rule-light: #c9c9c9;
    --band-blue: #0a58a8;
    --field-blue: #0d50f0;
    --brand-blue: #1a4c9c;
    --ink-light: #ffffff;
  }
  * { margin: 0; padding: 0; box-sizing: border-box; }
  html, body {
    width: 1200px; height: 888px; overflow: hidden;
    background: var(--page);
  }
  .card {
    position: absolute; left: 80px; top: 144px;
    width: 1040px; height: 600px; overflow: hidden;
    box-shadow: 0 6px 18px rgba(0,0,0,0.35);
    font-family: "Arimo", Arial, sans-serif;
    font-weight: 700;
    color: var(--ink-light);
  }
  .brand-panel {
    position: absolute; left: 0; top: 0; width: 100%; height: 300px;
    background: radial-gradient(ellipse at 45% 45%, var(--grey-light) 0%, var(--grey-mid) 55%, var(--grey-dark) 100%);
  }
  .brand-name {
    position: absolute; left: 0; right: 0; top: 78px;
    text-align: center; color: var(--brand-blue);
    text-transform: uppercase; line-height: 1.1;
  }
  .brand-name .line-main { display: block; font-size: 74px; letter-spacing: 2px; }
  .brand-name .line-sub { display: block; font-size: 38px; letter-spacing: 1px; margin-top: 6px; }
  .divider { position: absolute; left: 0; width: 100%; }
  .divider--top { top: 300px; height: 9px; background: var(--rule-light); }
  .divider--band { top: 309px; height: 24px; background: var(--band-blue); }
  .divider--bottom { top: 333px; height: 8px; background: var(--rule-light); }
  .contact-panel {
    position: absolute; left: 0; top: 341px; width: 100%; height: 259px;
    background: var(--field-blue);
  }
  .contact-rule {
    position: absolute; left: 62px; top: 22px; width: 2px; height: 200px;
    background: var(--ink-light);
  }
  .contact-heading { position: absolute; left: 96px; top: 24px; font-size: 26px; }
  .contact-heading .colon { margin-left: 24px; }
  .contact-person { position: absolute; left: 270px; top: 66px; font-size: 38px; }
  .contact-list {
    position: absolute; left: 86px; top: 118px; list-style: none;
    font-size: 26px; line-height: 30px;
  }
  .contact-list li { display: flex; }
  .contact-list .label { width: 118px; }
</style>
</head>
<body>
  <div class="card">
    <div class="brand-panel">
      <div class="brand-name">
        <span class="line-main">Eyelid Care Partners</span>
        <span class="line-sub">of the Brenton</span>
      </div>
    </div>
    <div class="divider divider--top"></div>
    <div class="divider divider--band"></div>
    <div class="divider divider--bottom"></div>
    <div class="contact-panel">
      <div class="contact-rule"></div>
      <div class="contact-heading">Contact<span class="colon">:</span></div>
      <div class="contact-person">Martin Delacourt, MD</div>
      <ul class="contact-list">
        <li><span class="label">Address</span><span>: 2718 Harborview Lane, Suite 206 Lakemont, VT 28517</span></li>
        <li><span class="label">Phone</span><span>: 555 - 555 - 0193</span></li>
        <li><span class="label">Fax</span><span>: 555 - 555 - 0194</span></li>
        <li><span class="label">web</span><span>: www.brentonlidstudio.example</span></li>
      </ul>
    </div>
  </div>
</body>
</html>
```